Garland Custom Boats Website update

I would like an updated website to my current site (Garlandboats.com).
I have an updated logo i would like to incorporate.
24 pages , would like to integrate videos of the boats (that i can upload later)

Target Market(s)

Professional and Commercial boat owners

Industry/Entity Type

Custom Boat Manufacturing

Coding

Coded - Design and coding required

Number of Pages Required

5+ page

Font styles to use
Serif

Requirements
Must have
• Easy to read, well laid-out, and video integration
Nice to have
• Fresh up to date look

```html
<!DOCTYPE html>
<html lang="en">
<head>
<meta charset="utf-8">
<title>Garland Custom Boats</title>
<link rel="stylesheet" href="https://fonts.googleapis.com/css2?family=Montserrat:wght@400;600;700&family=Poppins:wght@300;400;500&display=swap">
<style>
:root{
  --navy:#0b3a9a;
  --navy-deep:#0a2f82;
  --red:#c8202a;
  --ink:#1f2430;
  --muted:#4a4f5c;
  --white:#ffffff;
  --footer:#0b0f1a;
  --bar:#1a45a8;
}
*{box-sizing:border-box;margin:0;padding:0}
html,body{width:1200px;height:4203px;overflow:hidden;background:var(--white)}
body{position:relative;font-family:'Poppins',sans-serif;color:var(--ink)}
.abs{position:absolute}
.heading{font-family:'Montserrat',sans-serif;font-weight:700;color:var(--navy);text-transform:uppercase;letter-spacing:.3px}
.eyebrow{font-family:'Montserrat',sans-serif;font-weight:700;font-size:11px;color:var(--red);text-transform:uppercase;letter-spacing:.3px}
.btn{display:flex;align-items:center;justify-content:center;background:var(--navy);color:var(--white);font-size:15px;text-transform:uppercase;border-radius:0 0 22px 0}
.photo{position:absolute}

/* header */
.site-header{position:absolute;left:0;top:0;width:1200px;height:135px;background:var(--white)}
.brand{position:absolute;left:112px;top:42px;font-family:'Montserrat',sans-serif;font-weight:700;color:var(--navy);line-height:1}
.brand .name{font-size:34px;letter-spacing:1px}
.brand .sub{font-size:11px;letter-spacing:2px;margin-top:4px}
.nav{position:absolute;top:58px;font-size:14px;color:#2a2f3a}
.nav.active{color:var(--navy);font-style:italic;font-weight:500}
.nav.active::before{content:"";position:absolute;left:0;right:-4px;top:-6px;height:2px;background:var(--red)}

/* hero */
.hero-photo{left:0;top:135px;width:1200px;height:523px;background:linear-gradient(180deg,#7aa8d6 0%,#9ab8cf 30%,#3c6d86 55%,#124a60 100%)}
.hero-card{position:absolute;left:112px;top:201px;width:590px;height:327px;background:rgba(255,255,255,.93)}
.hero-card h1{position:absolute;left:42px;top:42px;font-size:31px;line-height:47px}
.hero-card h1 span{color:var(--red)}
.hero-card p{position:absolute;left:42px;top:146px;width:530px;font-size:18px;line-height:30px;color:var(--muted)}
.hero-card .btn{position:absolute;left:42px;top:229px;width:186px;height:51px}

/* about */
.about-photo{left:112px;top:760px;width:451px;height:460px;background:linear-gradient(180deg,#c7a48a 0%,#8d98a6 45%,#e7ebee 60%,#3d5a6e 100%)}
.about-text{position:absolute;left:599px;top:754px;width:480px}
.about-text h2{font-size:30px;margin:10px 0 18px}
.about-text p{font-size:15px;line-height:29.5px;color:var(--muted);margin-bottom:12px}
.about-text .btn{width:246px;height:50px;margin-top:26px}

/* categories */
.cat-title{position:absolute;left:112px;top:1326px}
.cat-title h2{font-size:32px;margin-top:10px}
.tile{position:absolute;width:319px;height:315px}
.caption{position:absolute;left:442px;top:1657px;width:250px;height:62px;background:var(--white);border-radius:0 0 26px 0;padding:12px 13px}
.caption strong{display:block;font-family:'Montserrat',sans-serif;font-size:15px;color:var(--navy)}
.caption span{font-size:11px;color:var(--ink)}

/* why */
.why-title{position:absolute;left:112px;top:2167px}
.why-title h2{font-size:32px;margin-top:10px}
.why-item{position:absolute;left:112px;width:470px}
.why-item h3{font-family:'Montserrat',sans-serif;font-weight:600;font-size:17px;color:var(--ink);padding-left:36px;position:relative}
.why-item h3 svg{position:absolute;left:0;top:4px}
.why-item p{font-size:15px;line-height:23px;color:var(--muted);padding-left:37px;margin-top:8px}
.why-photo{left:625px;top:2188px;width:463px;height:450px;background:linear-gradient(180deg,#8dbfe4 0%,#6aa3cf 40%,#c99a3e 62%,#2d6e95 100%)}

/* clients */
.clients{position:absolute;left:0;top:2740px;width:1200px;height:397px;background:var(--navy);border-radius:0 0 52px 0}
.clients .eyebrow{position:absolute;top:50px;width:100%;text-align:center;color:var(--white)}
.clients h2{position:absolute;top:78px;width:100%;text-align:center;color:var(--white);font-size:30px}
.client{position:absolute;top:163px;width:220px;height:120px;background:var(--white);display:flex;align-items:center;justify-content:center;gap:10px;font-family:'Montserrat',sans-serif;font-weight:600;font-size:16px;color:var(--navy);text-align:center;padding:0 12px}
.client i{width:14px;height:14px;border-radius:50%;background:var(--navy);flex:none}
.arrow-btn{position:absolute;top:203px}
.dot{position:absolute;top:331px;width:9px;height:9px;border-radius:50%;background:var(--white)}

/* spotlight */
.spot-head{position:absolute;top:3214px;width:1200px;text-align:center}
.spot-head h2{font-size:32px;margin-top:10px}
.video{left:112px;top:3310px;width:977px;height:390px;border-radius:0 0 28px 0;background:linear-gradient(160deg,#4c6c86 0%,#2f526d 50%,#1f3e57 100%)}
.play{position:absolute;left:570px;top:3477px}
.spot-title{position:absolute;left:110px;top:3722px;font-family:'Montserrat',sans-serif;font-weight:400;font-size:24px;color:var(--ink)}
.spot-text{position:absolute;left:110px;top:3767px;width:985px;font-size:15px;line-height:28px;color:var(--muted)}

/* footer */
.footer{position:absolute;left:0;top:3934px;width:1200px;height:226px;background:var(--footer)}
.footer .brand{left:118px;top:62px;color:var(--white)}
.social{position:absolute;top:142px;width:28px;height:28px;border-radius:50%;background:var(--white)}
.fnav{position:absolute;top:68px;font-size:15px;color:var(--white)}
.news-label{position:absolute;left:670px;top:125px;font-size:15px;color:var(--white)}
.news-input{position:absolute;left:802px;top:115px;width:213px;height:41px;background:var(--white);font-size:13px;color:#555;padding:12px 20px}
.news-btn{position:absolute;left:1015px;top:115px;width:74px;height:41px;background:var(--bar);display:flex;align-items:center;justify-content:center}
.bottom-bar{position:absolute;left:0;top:4160px;width:1200px;height:43px;background:var(--bar);color:var(--white);font-size:13px}
.bottom-bar .l{position:absolute;left:116px;top:12px}
.bottom-bar .r{position:absolute;right:112px;top:12px}
</style>
</head>
<body>

<header class="site-header">
  <div class="brand"><div class="name">GARLAND</div><div class="sub">CUSTOM BOATS</div></div>
  <nav>
    <a class="abs nav active" style="left:388px">HOME</a>
    <a class="abs nav" style="left:479px">ABOUT US</a>
    <a class="abs nav" style="left:600px">BOATS
      <svg width="10" height="8" viewBox="0 0 10 8"><path d="M1 2l4 4 4-4" fill="none" stroke="#2a2f3a" stroke-width="1.5"/></svg></a>
    <a class="abs nav" style="left:705px">CONTACT US</a>
    <a class="abs nav" style="left:848px">LINKS</a>
    <a class="abs nav" style="left:934px">DRIVING DIRECTIONS</a>
  </nav>
</header>

<section>
  <div class="photo hero-photo" role="img" aria-label="Luxury motor yachts moored at a sunny marina"></div>
  <div class="hero-card">
    <h1 class="heading">Custom boats built to<br>perform. <span>Crafted to last.</span></h1>
    <p>Proudly hand-built in Harbor Bend, Gulf Coast, for professionals, explorers, and dreamers.</p>
    <a class="btn">View our work</a>
  </div>
</section>

<section>
  <div class="photo about-photo" role="img" aria-label="Center-console fiberglass boat on calm water at sunset"></div>
  <div class="about-text">
    <div class="eyebrow">About us</div>
    <h2 class="heading">Who we are</h2>
    <p>At Garland Custom Boats, we are more than boat builders — we’re craftsmen, innovators, and stewards of a proud family legacy. Based in Harbor Bend, Gulf Coast, we specialize in custom fiberglass vessels designed for purpose, precision, and performance.</p>
    <p>With decades of hands-on experience passed down through generations, we take pride in building every boat by hand — right here in the USA. From rugged research vessels to luxury yachts, we bring each client’s vision to life with unmatched attention to detail and a passion for the water.</p>
    <a class="btn">Learn about our story</a>
  </div>
</section>

<section>
  <div class="cat-title">
    <div class="eyebrow">Boat categories</div>
    <h2 class="heading">Our custom boat categories</h2>
  </div>
  <div class="tile" style="left:112px;top:1424px;background:linear-gradient(180deg,#9fb3a0 0%,#4aa0c4 45%,#1e6f98 100%)" role="img" aria-label="Center-console boat with bimini top near a rocky coast"></div>
  <div class="tile" style="left:442px;top:1424px;background:linear-gradient(180deg,#d9e3ea 0%,#aebfcc 55%,#3d6a8a 100%)" role="img" aria-label="Dive boat with passengers on deck"></div>
  <div class="tile" style="left:771px;top:1424px;background:linear-gradient(180deg,#5b8fc2 0%,#c9d6e0 55%,#1d4f82 100%)" role="img" aria-label="Expedition research ship near icebergs"></div>
  <div class="tile" style="left:112px;top:1751px;background:linear-gradient(180deg,#6d8aa6 0%,#c8cfd4 45%,#2b4e6a 100%)" role="img" aria-label="Passenger ferry cruising on open water"></div>
  <div class="tile" style="left:442px;top:1751px;background:linear-gradient(180deg,#2d8fc4 0%,#5ab6df 55%,#1e7bb4 100%)" role="img" aria-label="Small boat seen from above on clear blue water"></div>
  <div class="tile" style="left:771px;top:1751px;background:linear-gradient(180deg,#1a4f84 0%,#2b6aa0 50%,#0f3a66 100%)" role="img" aria-label="Luxury motor yacht speeding across the sea"></div>
  <div class="caption"><strong>Dive Boats</strong><span>Spacious, safe, and customizable</span></div>
</section>

<section>
  <div class="why-title">
    <div class="eyebrow">Why choose us</div>
    <h2 class="heading">Why choose Garland</h2>
  </div>
  <div class="why-item" style="top:2259px">
    <h3><svg width="22" height="14" viewBox="0 0 22 14"><path d="M1 7h19M14 1l6 6-6 6" fill="none" stroke="#0b3a9a" stroke-width="2"/></svg>Custom-Built, Not Mass-Produced</h3>
    <p>Every vessel is tailored to your unique purpose — from concept to completion.</p>
  </div>
  <div class="why-item" style="top:2357px">
    <h3><svg width="22" height="14" viewBox="0 0 22 14"><path d="M1 7h19M14 1l6 6-6 6" fill="none" stroke="#0b3a9a" stroke-width="2"/></svg>Precision &amp; Detail</h3>
    <p>We obsess over every joint, finish, and component for lasting quality and performance.</p>
  </div>
  <div class="why-item" style="top:2454px">
    <h3><svg width="22" height="14" viewBox="0 0 22 14"><path d="M1 7h19M14 1l6 6-6 6" fill="none" stroke="#0b3a9a" stroke-width="2"/></svg>Trusted by Professionals</h3>
    <p>Our boats serve TOA, universities, commercial divers, and serious anglers.</p>
  </div>
  <div class="why-item" style="top:2552px">
    <h3><svg width="22" height="14" viewBox="0 0 22 14"><path d="M1 7h19M14 1l6 6-6 6" fill="none" stroke="#0b3a9a" stroke-width="2"/></svg>Decades of Experience</h3>
    <p>Second-generation boat builders with a legacy of innovation and craftsmanship.</p>
  </div>
  <div class="photo why-photo" role="img" aria-label="Family relaxing on the bow of a yellow sport boat on a lake"></div>
</section>

<section class="clients">
  <div class="eyebrow">Our clients</div>
  <h2 class="heading">Organizations we’ve served</h2>
  <svg class="arrow-btn" style="left:43px" width="40" height="40" viewBox="0 0 40 40"><circle cx="20" cy="20" r="19" fill="none" stroke="#fff" stroke-width="1.5"/><path d="M23 13l-7 7 7 7" fill="none" stroke="#fff" stroke-width="1.8"/></svg>
  <div class="client" style="left:112px"><i></i>Tidewater Ocean Agency</div>
  <div class="client" style="left:365px">Harborline Yachting</div>
  <div class="client" style="left:617px">Meridian Cruises</div>
  <div class="client" style="left:870px">Coralia Voyages</div>
  <svg class="arrow-btn" style="left:1120px" width="40" height="40" viewBox="0 0 40 40"><circle cx="20" cy="20" r="19" fill="none" stroke="#fff" stroke-width="1.5"/><path d="M17 13l7 7-7 7" fill="none" stroke="#fff" stroke-width="1.8"/></svg>
  <span class="dot" style="left:574px"></span>
  <span class="dot" style="left:592px"></span>
  <span class="dot" style="left:608px;width:14px;height:14px;top:329px"></span>
</section>

<section>
  <div class="spot-head">
    <div class="eyebrow">Boat spotlight</div>
    <h2 class="heading">Built for purpose</h2>
  </div>
  <div class="photo video" role="img" aria-label="Video still of a motor cruiser running at speed, leaving a white wake"></div>
  <svg class="play" width="56" height="56" viewBox="0 0 56 56"><circle cx="28" cy="28" r="26" fill="none" stroke="#fff" stroke-width="3"/><path d="M22 17l16 11-16 11z" fill="#fff"/></svg>
  <h3 class="spot-title">Vessel Highlight: 46' Research Vessel – Gulf Coast University</h3>
  <p class="spot-text">Purpose-built for marine exploration, this custom 46-foot research vessel features a reinforced fiberglass hull, A-frame and jib boom, and advanced instrumentation compatibility. Designed in close collaboration with university researchers, it supports fieldwork in both shallow and deep-water environments.</p>
</section>

<footer class="footer">
  <div class="brand"><div class="name">GARLAND</div><div class="sub">CUSTOM BOATS</div></div>
  <span class="social" style="left:119px" aria-label="Social link"></span>
  <span class="social" style="left:158px" aria-label="Social link"></span>
  <span class="social" style="left:197px" aria-label="Social link"></span>
  <span class="social" style="left:236px" aria-label="Social link"></span>
  <span class="social" style="left:276px" aria-label="Social link"></span>
  <a class="fnav" style="left:418px">HOME</a>
  <a class="fnav" style="left:501px">ABOUT US</a>
  <a class="fnav" style="left:616px">BOATS</a>
  <a class="fnav" style="left:709px">CONTACT US</a>
  <a class="fnav" style="left:842px">LINKS</a>
  <a class="fnav" style="left:921px">DRIVING DIRECTIONS</a>
  <div class="news-label">NEWSLETTER</div>
  <div class="news-input">Enter you email</div>
  <div class="news-btn"><svg width="30" height="14" viewBox="0 0 30 14"><path d="M1 7h26M21 1l6 6-6 6" fill="none" stroke="#fff" stroke-width="2.5"/></svg></div>
</footer>
<div class="bottom-bar">
  <span class="l">Copyrights @ 2025 Garland Boats - All Rights</span>
  <span class="r">Terms &amp; Conditions - Privacy Policy</span>
</div>

</body>
</html>
```